Stationery for use with Ninefold Ridge reports

I would like to get a stationery design that my firm -- Ninefold Ridge Advisory -- will use as a format for reports that we send our clients. I am specifically looking for a design for use on a piece of paper or letterhead -- not business cards or envelopes.

We are an Africa based US risk intelligence and strategy firm that works with multinational corporations operating in West Africa. Our initial thinking is that we would like a color scheme consistent with our existing logo -- however we are open to other color schemes.

Also, we would like to see at least two separate versions: one with our company name and logo, the other without name and logo.

We also would like font recommendations for the stationary design.

The final design should communicate discreet professionalism and a modern approach, but it should not overshadow the words and information printed on the stationery.

Target Market(s)

Multinational corporations that currently use our products.

Font styles to use
Serif
Sans Serif

Requirements
Must have
• Sense of discreet professionalism that will not overshadow the content we put onto the stationery format.
• We would like to see designs with and without our company name/logo.
• Please suggest fonts that would work with the stationery.
Nice to have
• Ideally colors consistent with out existing logo, though we are open to and even encourage other ideas.
Should not have
• No need for business cards or envelopes.

```html
<!DOCTYPE html>
<html lang="en">
<head>
<meta charset="utf-8">
<title>Ninefold Ridge Advisory — Letterhead</title>
<link rel="stylesheet" href="https://fonts.googleapis.com/css2?family=Source+Sans+3:wght@300;400;700&display=swap">
<style>
  :root {
    --backdrop: #d0ebf3;
    --paper: #ffffff;
    --navy: #233f4d;
    --ochre: #b0792e;
    --sky: #a8d6ef;
    --body-text: #5a5a5a;
    --signature-ink: #dcdcdc;
    --footer-text: #f3f3f3;
  }
  * { box-sizing: border-box; margin: 0; padding: 0; }
  html, body {
    width: 1200px; height: 1200px; overflow: hidden;
    background: var(--backdrop);
    font-family: "Source Sans 3", Arial, sans-serif;
  }
  .sheet {
    position: absolute; left: 242px; top: 95px;
    width: 716px; height: 1011px;
    background: var(--paper);
    box-shadow: 1px 2px 4px rgba(0,0,0,0.18);
  }
  .brand {
    position: absolute; top: 118px; left: 0; width: 100%;
    display: flex; align-items: center; justify-content: center; gap: 10px;
    color: var(--navy); font-weight: 700; font-size: 28px; line-height: 36px;
  }
  .brand-mark { width: 16px; height: 16px; background: var(--ochre); }
  .letter {
    position: absolute; left: 72px; top: 300px; width: 600px;
    color: var(--body-text); font-size: 13px; font-weight: 400;
  }
  .letter-date { line-height: 20px; margin-bottom: 37px; }
  .letter p { line-height: 26px; }
  .letter p span { display: block; white-space: nowrap; }
  .letter p + p { margin-top: 3px; }
  .letter p.para-3 { margin-top: 5px; }
  .letter p.para-4 { margin-top: 9px; }
  .signoff {
    position: absolute; left: 503px; top: 696px;
    color: var(--body-text); font-size: 13px; line-height: 14px;
  }
  .signature-area {
    width: 140px; height: 42px; margin-bottom: 8px;
    background: var(--signature-ink); border-radius: 3px;
  }
  .footer-rule {
    position: absolute; left: 0; top: 932px; width: 100%; height: 8px;
    background: var(--sky);
  }
  .footer-contact, .footer-address {
    position: absolute; top: 946px; height: 65px;
    color: var(--footer-text); font-size: 12.5px; font-weight: 300; line-height: 15px;
  }
  .footer-contact { left: 0; width: 355px; background: var(--navy); padding: 10px 0 0 37px; }
  .footer-address { left: 362px; width: 354px; background: var(--ochre); padding: 10px 37px 0 0; text-align: right; }
  .contact-line { display: flex; align-items: center; gap: 7px; }
  .contact-line svg { width: 9px; height: 9px; fill: var(--footer-text); }
</style>
</head>
<body>
  <main class="sheet">
    <header class="brand">
      <span class="brand-mark"></span>
      <span class="brand-name">Ninefold Ridge Advisory</span>
    </header>

    <section class="letter">
      <div class="letter-date">Date, 10 September, 2020</div>
      <p class="para-1">
        <span>This is a sample letter that has been placed to demonstrate typing remat (Your Company). letterhead</span>
        <span>design. When positioned properly, it will serve to work in harmony with all other elements letterhead.</span>
        <span>This letterhead design is meant to project an image</span>
      </p>
      <p class="para-2">
        <span>This letterhead design is meant project an image of professionalism reliability. By using simple aligen</span>
        <span>we have created a very spacious feeling. The simplicity suggest&nbsp; rengththe spaciousnes contributes h</span>
        <span>aesthetics the layout. These basic qualities along with the (Your Company)</span>
      </p>
      <p class="para-3">
        <span>look and helps reinforce the (Your Company) brand. letterhead design is meant to project an image p</span>
        <span>design. When positioned properly, it will serve to work in harmony all the other elements letterhead.</span>
        <span>sionalism and reliability.</span>
      </p>
      <p class="para-4">
        <span>This letterhead design is based on the (Form of your logo) form (Your Company) logo. Each stationery</span>
        <span>we have created a very spacious feeling. The simplicity suggests strength the spaciousnes contribute</span>
        <span>part of the (Form of your logo).</span>
      </p>
    </section>

    <div class="signoff">
      <div class="signature-area" role="img" aria-label="Handwritten signature of Marcus Eldridge"></div>
      <div class="signer-name">Marcus Eldridge</div>
      <div class="signer-title">Manager</div>
    </div>

    <div class="footer-rule"></div>
    <footer>
      <div class="footer-contact">
        <div class="contact-line">
          <svg viewBox="0 0 10 10"><path d="M2 0.5l1.6 2-0.9 1.1c0.6 1.3 1.4 2.1 2.7 2.7l1.1-0.9 2 1.6-1 1.9C4 8.6 1.4 6 0.1 1.5z"/></svg>
          <span>555-014-2100</span>
        </div>
        <div class="contact-line">
          <svg viewBox="0 0 10 10"><path d="M0 2h10v0.8L5 5.6 0 2.8z M0 3.9l5 2.8 5-2.8V8H0z"/></svg>
          <span>youremail@mailhost.com</span>
        </div>
        <div class="contact-line">
          <svg viewBox="0 0 10 10"><circle cx="5" cy="5" r="4.5"/></svg>
          <span>www.yourwebsite.com</span>
        </div>
      </div>
      <div class="footer-address">
        <div>Your address</div>
        <div>city</div>
        <div>state, ZIP 0000</div>
      </div>
    </footer>
  </main>
</body>
</html>
```